Business Card Design

Electronic Security Installation Specialists

Check out our website at www.tallbrookllc.com to see what we do.

Industry/Entity Type

Business

Contact Information for Business Card

Tall Brook
Marjorie Hadley
281 Orchard Rise
Mapleton, WV 25871

Colors
3176b5
0455a3
ffffff

```html
<!DOCTYPE html>
<html lang="en">
<head>
<meta charset="utf-8">
<title>Tall Brook — Business Card</title>
<link rel="stylesheet" href="https://fonts.googleapis.com/css2?family=Aldrich&display=swap">
<style>
  :root {
    --brand-blue: #0455a3;
    --brand-blue-light: #3176b5;
    --brand-blue-deep: #1f4a8f;
    --paper: #ffffff;
    --paper-shade: #e4e5e7;
    --swoosh-grey: #8c8d90;
    --stage: #d9dadc;
    --ink-light: #ffffff;
  }
  * { box-sizing: border-box; margin: 0; padding: 0; }
  html, body {
    width: 1200px; height: 900px; overflow: hidden;
    background: var(--stage);
  }
  .card {
    position: absolute; left: 100px; top: 165px;
    width: 1000px; height: 570px;
    border-radius: 48px; overflow: hidden;
    box-shadow: 0 10px 30px rgba(0,0,0,.18);
    font-family: "Aldrich", sans-serif;
    color: var(--ink-light);
    font-variant: small-caps;
  }
  .card__art { position: absolute; inset: 0; }
  .logo {
    position: absolute; left: 340px; top: 40px;
    width: 160px; height: 160px; border-radius: 50%;
    background: var(--brand-blue);
    border: 6px solid var(--paper);
    box-shadow: 0 0 0 2px #b9babd, 0 4px 10px rgba(0,0,0,.25);
    display: flex; align-items: center; justify-content: center;
  }
  .logo__name {
    font-family: "Aldrich", sans-serif;
    font-variant: normal;
    font-size: 27px; color: var(--ink-light);
    letter-spacing: 1px;
  }
  .identity {
    position: absolute; right: 500px; top: 330px;
    text-align: right; line-height: 1.35;
  }
  .identity__name { font-size: 24px; letter-spacing: 2px; }
  .identity__role { font-size: 20px; letter-spacing: 1.5px; opacity: .92; }
  .identity__address { margin-top: 32px; font-size: 20px; letter-spacing: 1.5px; line-height: 1.5; }
  .divider {
    position: absolute; left: 520px; top: 318px;
    width: 2px; height: 176px; background: rgba(255,255,255,.7);
  }
  .contacts {
    position: absolute; left: 545px; top: 316px;
    list-style: none; font-size: 21px; letter-spacing: 1.5px;
  }
  .contacts__item { display: flex; align-items: center; gap: 10px; height: 32px; }
  .contacts__item--gap { margin-top: 16px; }
  .contacts__icon { width: 20px; height: 20px; flex: none; }
</style>
</head>
<body>
  <section class="card" aria-label="Tall Brook business card">
    <svg class="card__art" viewBox="0 0 1000 570" width="1000" height="570" aria-hidden="true">
      <defs>
        <linearGradient id="paperGrad" x1="0" y1="0" x2="0.3" y2="1">
          <stop offset="0" stop-color="#fafafa"/>
          <stop offset="1" stop-color="#dcdde0"/>
        </linearGradient>
        <radialGradient id="bandGrad" cx="0.5" cy="0.6" r="0.7">
          <stop offset="0" stop-color="#3176b5"/>
          <stop offset="0.6" stop-color="#245ea3"/>
          <stop offset="1" stop-color="#1f4a8f"/>
        </radialGradient>
      </defs>
      <rect class="card__paper" width="1000" height="570" fill="url(#paperGrad)"/>
      <path class="card__swoosh" d="M0,432 C250,345 600,236 1000,150 L1000,166 C600,252 250,362 0,446 Z" fill="var(--swoosh-grey)"/>
      <path class="card__band" d="M0,446 C250,362 600,252 1000,166 L1000,570 L0,570 Z" fill="url(#bandGrad)"/>
    </svg>

    <div class="logo"><span class="logo__name">Tall Brook</span></div>

    <div class="identity">
      <p class="identity__name">Marjorie Hadley</p>
      <p class="identity__role">Owner / C.E.O</p>
      <p class="identity__address">281 Orchard Rise,<br>Mapleton, WV 25871</p>
    </div>

    <div class="divider"></div>

    <ul class="contacts">
      <li class="contacts__item">
        <svg class="contacts__icon" viewBox="0 0 20 20"><circle cx="10" cy="10" r="10" fill="#fff"/><path d="M6.5 5.5l2 2-1 1.2c.7 1.5 1.8 2.6 3.3 3.3l1.2-1 2 2-1.3 1.5C9.6 14.3 5.7 10.4 5.3 7z" fill="var(--brand-blue)"/></svg>
        304-555-0142
      </li>
      <li class="contacts__item">
        <svg class="contacts__icon" viewBox="0 0 20 20"><circle cx="10" cy="10" r="10" fill="#fff"/><rect x="5.5" y="7" width="9" height="7" rx="1" fill="var(--brand-blue)"/><rect x="7" y="4.5" width="6" height="3" fill="var(--brand-blue)"/></svg>
        304-555-0187
      </li>
      <li class="contacts__item">
        <svg class="contacts__icon" viewBox="0 0 20 20"><circle cx="10" cy="10" r="10" fill="#fff"/><rect x="7" y="4.5" width="6" height="11" rx="1.2" fill="var(--brand-blue)"/><rect x="8" y="6" width="4" height="6.5" fill="#fff"/></svg>
        304-555-0119
      </li>
      <li class="contacts__item contacts__item--gap">
        <svg class="contacts__icon" viewBox="0 0 20 20"><circle cx="10" cy="10" r="10" fill="#fff"/><rect x="5" y="6.5" width="10" height="7" fill="var(--brand-blue)"/><path d="M5 6.5l5 4 5-4" fill="none" stroke="#fff" stroke-width="1"/></svg>
        info@tallbrookllc.com
      </li>
      <li class="contacts__item">
        <svg class="contacts__icon" viewBox="0 0 20 20"><circle cx="10" cy="10" r="10" fill="#fff"/><circle cx="10" cy="10" r="5.5" fill="none" stroke="var(--brand-blue)" stroke-width="1.3"/><path d="M4.5 10h11M10 4.5c-2.5 3-2.5 8 0 11M10 4.5c2.5 3 2.5 8 0 11" fill="none" stroke="var(--brand-blue)" stroke-width="1.1"/></svg>
        www.tallbrookllc.com
      </li>
    </ul>
  </section>
</body>
</html>
```